Business card for Luxury Portable Restroom Trailer company

We are a Luxury Portable Restroom Trailer Company Called FALCRIDGE HIRES. Based in Orange County California. We provide portable restroom trailers for events, such as, Weddings, Concerts, Charity events, Sporting events, Tournaments, Corporate events, ect. We rent and Sell the Luxury restrooms. Our colors are white, grey, and Orange. As you will see in the logo we uploaded.
There are 2 people in the company so the names and titles will change for the 3 people but card will remain the same. Here is the information for each Person: Dwight Penner CFO 555 318-0476
next Person: Leon Marchetti VP 555 318-0476
Next Person: Owen Marchetti CEO 555 318-0476
Information to include on the card: Luxury Restroom Trailers Rental and Sales. Weddings, Concerts, Charity, Sporting and Corp. Events.

```html
<!DOCTYPE html>
<html lang="en">
<head>
<meta charset="utf-8">
<title>Falcridge Hires — Business Card</title>
<link rel="stylesheet" href="https://fonts.googleapis.com/css2?family=Montserrat:wght@400;500;700;800&display=swap">
<style>
  :root {
    --orange: #f26d24;
    --white: #ffffff;
    --backdrop: #dcdcdc;
    --shadow: rgba(0, 0, 0, 0.18);
  }
  * { box-sizing: border-box; margin: 0; padding: 0; }
  html, body {
    width: 1200px;
    height: 856px;
    overflow: hidden;
    background: var(--backdrop);
    font-family: "Montserrat", Arial, sans-serif;
  }
  .sheet {
    width: 1200px;
    height: 856px;
    display: flex;
    align-items: center;
    justify-content: center;
    gap: 40px;
  }
  .card {
    position: relative;
    width: 540px;
    height: 309px;
    background: var(--orange);
    color: var(--white);
    overflow: hidden;
    box-shadow: 0 10px 28px var(--shadow);
  }

  /* Contact side */
  .card--contact .white-band {
    position: absolute;
    top: 0; right: 0;
    width: 150px;
    height: 100%;
    background: var(--white);
  }
  .card--contact .emblem {
    position: absolute;
    top: 50%;
    left: 390px;
    width: 232px;
    height: 232px;
    transform: translate(-50%, -50%);
    border-radius: 50%;
    background: var(--orange);
    display: flex;
    align-items: center;
    justify-content: center;
  }
  .emblem .ring {
    width: 210px;
    height: 210px;
    border-radius: 50%;
    border: 9px solid var(--white);
    display: flex;
    align-items: center;
    justify-content: center;
  }
  .emblem .disc {
    width: 176px;
    height: 176px;
    border-radius: 50%;
    background: var(--white);
    display: flex;
    align-items: center;
    justify-content: center;
    text-align: center;
    color: var(--orange);
    font-weight: 800;
    font-size: 21px;
    line-height: 1.1;
    letter-spacing: 0.5px;
  }
  .contact-block {
    position: absolute;
    top: 26px;
    left: 30px;
  }
  .brand-name--small {
    font-weight: 800;
    font-size: 19px;
    letter-spacing: 1px;
    line-height: 1.05;
    margin-bottom: 16px;
  }
  .person { margin-bottom: 9px; }
  .person__name {
    font-weight: 800;
    font-size: 15px;
    text-transform: uppercase;
    letter-spacing: 0.6px;
  }
  .person__title {
    font-weight: 400;
    font-size: 12px;
    margin-top: 1px;
  }
  .person__phone {
    display: flex;
    align-items: center;
    gap: 6px;
    font-size: 12px;
    font-weight: 500;
    margin-top: 1px;
  }
  .person__phone svg { width: 12px; height: 12px; fill: var(--white); }

  /* Brand side */
  .card--brand {
    display: flex;
    flex-direction: column;
    align-items: center;
    justify-content: center;
    text-align: center;
  }
  .brand-name--large {
    font-weight: 800;
    font-size: 44px;
    letter-spacing: 2px;
    line-height: 1;
  }
  .brand-name--large .sub {
    display: block;
    font-size: 28px;
    letter-spacing: 6px;
    margin-top: 8px;
  }
  .services {
    margin-top: 44px;
    font-size: 13.5px;
    font-weight: 500;
    line-height: 1.7;
    list-style: none;
  }
  .services li { display: inline; }
  .services li::before {
    content: "";
    display: inline-block;
    width: 7px;
    height: 7px;
    border-radius: 50%;
    background: var(--white);
    margin: 0 6px 2px 8px;
    vertical-align: middle;
  }
</style>
</head>
<body>
<main class="sheet">

  <section class="card card--contact">
    <div class="white-band"></div>
    <div class="emblem">
      <div class="ring">
        <div class="disc">FALCRIDGE<br>HIRES</div>
      </div>
    </div>

    <div class="contact-block">
      <div class="brand-name--small">FALCRIDGE<br>HIRES</div>

      <div class="person">
        <div class="person__name">Dwight Penner</div>
        <div class="person__title">CFO</div>
        <div class="person__phone">
          <svg viewBox="0 0 24 24" aria-hidden="true"><path d="M6.6 10.8a15.1 15.1 0 0 0 6.6 6.6l2.2-2.2a1 1 0 0 1 1-.25 11.4 11.4 0 0 0 3.6.57 1 1 0 0 1 1 1V20a1 1 0 0 1-1 1A17 17 0 0 1 3 4a1 1 0 0 1 1-1h3.5a1 1 0 0 1 1 1c0 1.25.2 2.45.57 3.57a1 1 0 0 1-.25 1z"/></svg>
          <span>555 318-0476</span>
        </div>
      </div>

      <div class="person">
        <div class="person__name">Leon Marchetti</div>
        <div class="person__title">VP</div>
        <div class="person__phone">
          <svg viewBox="0 0 24 24" aria-hidden="true"><path d="M6.6 10.8a15.1 15.1 0 0 0 6.6 6.6l2.2-2.2a1 1 0 0 1 1-.25 11.4 11.4 0 0 0 3.6.57 1 1 0 0 1 1 1V20a1 1 0 0 1-1 1A17 17 0 0 1 3 4a1 1 0 0 1 1-1h3.5a1 1 0 0 1 1 1c0 1.25.2 2.45.57 3.57a1 1 0 0 1-.25 1z"/></svg>
          <span>555 318-0476</span>
        </div>
      </div>

      <div class="person">
        <div class="person__name">Owen Marchetti</div>
        <div class="person__title">CEO</div>
        <div class="person__phone">
          <svg viewBox="0 0 24 24" aria-hidden="true"><path d="M6.6 10.8a15.1 15.1 0 0 0 6.6 6.6l2.2-2.2a1 1 0 0 1 1-.25 11.4 11.4 0 0 0 3.6.57 1 1 0 0 1 1 1V20a1 1 0 0 1-1 1A17 17 0 0 1 3 4a1 1 0 0 1 1-1h3.5a1 1 0 0 1 1 1c0 1.25.2 2.45.57 3.57a1 1 0 0 1-.25 1z"/></svg>
          <span>555 318-0476</span>
        </div>
      </div>
    </div>
  </section>

  <section class="card card--brand">
    <div class="brand-name--large">FALCRIDGE<span class="sub">HIRES</span></div>
    <ul class="services">
      <li>Luxury Restroom Trailers Rental and Sales</li><br>
      <li>Weddings</li><li>Concerts</li><li>Charity</li><li>Sporting and Corp</li><li>Events</li>
    </ul>
  </section>

</main>
</body>
</html>
```